Audio-Visual & Video Communications Business Requires a Cutting-edge Business Card Design

LinkVerra is a new Audio-Visual & Video Communications company in Cape Town, South Africa that is looking for a cutting-edge business card design. We sell these products to the Corporate, Education & Hospitality markets and will also host an Online Shop for companies and individuals to purchase our products online.

We are already using the following two colours in our logo and draft website. Please incorporate these colours into the design. Please note that our website is still in the design stage if you need to visit it. Green #a0ce4e & Dark Grey #333333.

Hi,

Please note that I have uploaded our logo in an .eps format.

Target Market(s)

Corporate Companies, Education Institutions & Hospitality Markets

Industry/Entity Type

Business

Requirements
Nice to have
• It would be great if you could incorporate the services that we offer.

1. Consultation & Design
2. Project Management
3. Supply & Installation
4. Onsite Support Personal
5. Online Shop

```html
<!DOCTYPE html>
<html lang="en">
<head>
<meta charset="utf-8">
<title>LinkVerra Business Card</title>
<link rel="stylesheet" href="https://fonts.googleapis.com/css2?family=Open+Sans:wght@400;600;700&family=Arimo:wght@400&display=swap">
<style>
  :root {
    --green: #a0ce4e;
    --dark-grey: #333333;
    --card-dark: #1f1f1f;
    --card-white: #f7f7f7;
    --mid-grey: #5a5a5a;
    --text-grey: #3a3a3a;
    --backdrop: #2a2a2a;
  }
  * { margin: 0; padding: 0; box-sizing: border-box; }
  html, body { width: 1200px; height: 900px; overflow: hidden; }
  body {
    background: var(--backdrop);
    font-family: "Open Sans", Arial, sans-serif;
    position: relative;
  }
  .card {
    position: absolute;
    width: 560px;
    height: 320px;
    border-radius: 2px;
    box-shadow: 0 14px 36px rgba(0,0,0,0.5);
  }

  /* Front card */
  .card-front {
    left: 110px;
    top: 100px;
    background: var(--card-white);
  }
  .front-brand {
    position: absolute;
    right: 40px;
    top: 38px;
    display: flex;
    align-items: center;
    gap: 14px;
  }
  .brand-name {
    font-weight: 700;
    color: var(--green);
    letter-spacing: 0.2px;
    white-space: nowrap;
  }
  .front-brand .brand-name { font-size: 34px; }
  .brand-dot {
    flex: none;
    width: 52px;
    height: 52px;
    border-radius: 50%;
    background: var(--green);
  }
  .contact-list {
    position: absolute;
    right: 40px;
    top: 116px;
    list-style: none;
    font-family: "Arimo", Arial, sans-serif;
    font-size: 11.5px;
    color: var(--text-grey);
    line-height: 18px;
  }
  .contact-list li {
    display: flex;
    justify-content: flex-end;
    align-items: center;
    gap: 8px;
    white-space: nowrap;
  }
  .contact-icon { flex: none; width: 10px; height: 10px; fill: var(--green); }
  .person {
    position: absolute;
    left: 40px;
    bottom: 42px;
  }
  .person-name {
    font-size: 22px;
    font-weight: 700;
    color: var(--green);
    line-height: 1.1;
  }
  .person-title {
    font-size: 12px;
    color: var(--text-grey);
    margin-top: 2px;
  }

  /* Back card */
  .card-back {
    left: 530px;
    top: 480px;
    background: var(--card-dark);
    display: flex;
    flex-direction: column;
    align-items: center;
    justify-content: center;
  }
  .back-brand {
    display: flex;
    flex-direction: column;
    align-items: center;
    gap: 10px;
  }
  .card-back .brand-name { font-size: 40px; line-height: 1.1; }
  .card-back .brand-dot { width: 62px; height: 62px; }
  .services {
    margin-top: 14px;
    text-align: center;
    font-size: 13.5px;
    line-height: 20px;
    color: var(--green);
  }
  .services .sep { margin: 0 6px; }
  .services .muted { color: var(--mid-grey); }
</style>
</head>
<body>

  <section class="card card-front">
    <div class="front-brand">
      <span class="brand-name">LinkVerra</span>
      <span class="brand-dot"></span>
    </div>

    <ul class="contact-list">
      <li>+ 27 21 480 3156
        <svg class="contact-icon" viewBox="0 0 10 10"><path d="M2 0h2l1 3-1.5 1a6 6 0 0 0 2.5 2.5L7 5l3 1v2a2 2 0 0 1-2 2A8 8 0 0 1 0 2a2 2 0 0 1 2-2z"/></svg>
      </li>
      <li>+ 27 82 614 9027
        <svg class="contact-icon" viewBox="0 0 10 10"><rect x="2.5" y="0" width="5" height="10" rx="1"/></svg>
      </li>
      <li>info@LinkVerra.com
        <svg class="contact-icon" viewBox="0 0 10 10"><rect x="0" y="2" width="10" height="6" rx="1"/></svg>
      </li>
      <li>www.LinkVerra.com
        <svg class="contact-icon" viewBox="0 0 10 10"><circle cx="5" cy="5" r="4.5"/></svg>
      </li>
    </ul>

    <div class="person">
      <p class="person-name">Marissa Kole</p>
      <p class="person-title">Managing Director</p>
    </div>
  </section>

  <section class="card card-back">
    <div class="back-brand">
      <span class="brand-dot"></span>
      <span class="brand-name">LinkVerra</span>
    </div>
    <p class="services">
      Consultation &amp; Design<span class="sep">|</span><span class="muted">Project Management</span><span class="sep">|</span>Supply &amp; Installation<br>
      Onsite Support Personal<span class="sep">|</span>Online Shop
    </p>
  </section>

</body>
</html>
```